VENTURE CAPITAL GROUP BUSINESS CARD DESIGN

Venture Capital Group based in SF looking for a bold business card design. No trendy colour explosion, 3D effects etc. Just "simple" optical effects. Works on your brain, keeps your eye focused and sticks to your mind.
Target Market(s)
Technology startups
Industry/Entity Type
Venture Capital
Contact Information for Business Card
DESMOND WHITLAKE
MANAGING PARTNER
187 FENWORTH ST SAN FRANCISCO, CA 94187
415.555.0142 O
415.555.0147 F
415.555.0193 C
desmond@veldtmoorcapital.ventures

```html
<!DOCTYPE html>
<html lang="en">
<head>
<meta charset="utf-8">
<title>Veldtmoor Capital Group – Business Card</title>
<link rel="stylesheet" href="https://fonts.googleapis.com/css2?family=Source+Sans+3:wght@400;600;700&display=swap">
<style>
  :root {
    --backdrop: #3b3633;
    --card: #ffffff;
    --card-shade: #f1f3f1;
    --green: #1f8a2e;
    --green-dark: #146b22;
    --green-light: #3fae4a;
    --ink: #1c1c1c;
    --muted: #6d6d6d;
  }
  * { box-sizing: border-box; margin: 0; padding: 0; }
  html, body {
    width: 1200px; height: 844px; overflow: hidden;
    background: var(--backdrop);
    font-family: "Source Sans 3", Arial, sans-serif;
  }
  .stage {
    position: relative; width: 1200px; height: 844px;
    display: flex; align-items: center; justify-content: center; gap: 60px;
  }
  .card {
    position: relative; width: 510px; height: 292px;
    background: linear-gradient(135deg, var(--card-shade) 0%, var(--card) 45%);
    box-shadow: 0 10px 24px rgba(0,0,0,.45);
    overflow: hidden;
  }

  /* Contact side */
  .band {
    position: absolute; left: 0; right: 0; height: 14px;
    background: linear-gradient(180deg, var(--green-light), var(--green-dark));
  }
  .band--top { top: 0; }
  .band--bottom { bottom: 0; }
  .contact {
    position: absolute; left: 215px; top: 62px;
  }
  .contact__name {
    color: var(--green); font-weight: 700; font-size: 22px; line-height: 1;
  }
  .contact__title {
    color: var(--ink); font-size: 14px; margin: 4px 0 22px 38px;
  }
  .contact__list { list-style: none; }
  .contact__item {
    display: flex; align-items: center; gap: 7px;
    font-size: 15px; color: var(--ink); line-height: 21px;
  }
  .contact__item--phone { padding-left: 50px; }
  .contact__item--email { margin-top: 3px; }
  .contact__item--address { padding-left: 20px; }
  .icon { width: 12px; height: 12px; fill: var(--green); flex: none; }

  /* Brand side */
  .tab {
    position: absolute; width: 34px; height: 40px;
    background: linear-gradient(90deg, var(--green-dark), var(--green-light));
    box-shadow: -2px 0 0 #d8d8d8;
  }
  .tab--right { right: 0; top: 36px; }
  .tab--left { left: 0; top: 150px; box-shadow: 2px 0 0 #d8d8d8; }
  .brand {
    position: absolute; inset: 0;
    display: flex; flex-direction: column; align-items: center; justify-content: center;
    gap: 14px;
  }
  .brand__dot {
    width: 58px; height: 58px; border-radius: 50%;
    background: var(--green);
  }
  .brand__name {
    color: var(--green); font-weight: 600; font-size: 30px;
    letter-spacing: 2px; line-height: 1; text-align: center;
  }
</style>
</head>
<body>
<main class="stage">

  <section class="card card--contact" aria-label="Contact side">
    <div class="band band--top"></div>
    <div class="contact">
      <h1 class="contact__name">Desmond Whitlake</h1>
      <p class="contact__title">Managing Partner</p>
      <ul class="contact__list">
        <li class="contact__item contact__item--phone">
          <svg class="icon" viewBox="0 0 12 12" aria-hidden="true"><path d="M2.5 0.5l2 2-1 1.5c.6 1.4 1.9 2.7 3.5 3.5l1.5-1 2 2-1.5 2C4.5 10 2 7.5 0.5 2z"/></svg>
          415.555.0142
        </li>
        <li class="contact__item contact__item--phone">
          <svg class="icon" viewBox="0 0 12 12" aria-hidden="true"><rect x="1" y="4" width="10" height="6" rx="1"/><rect x="3" y="1" width="6" height="3" fill="#fff" stroke="#1f8a2e"/></svg>
          415.555.0147
        </li>
        <li class="contact__item contact__item--phone">
          <svg class="icon" viewBox="0 0 12 12" aria-hidden="true"><rect x="3" y="0.5" width="6" height="11" rx="1"/><rect x="4" y="2" width="4" height="7" fill="#fff"/></svg>
          415.555.0193
        </li>
        <li class="contact__item contact__item--email">
          <svg class="icon" viewBox="0 0 12 12" aria-hidden="true"><rect x="0.5" y="2" width="11" height="8"/><path d="M0.5 2l5.5 4.5L11.5 2" fill="none" stroke="#fff"/></svg>
          desmond@veldtmoorcapital.ventures
        </li>
        <li class="contact__item contact__item--address">
          187 Fenworth St San Francisco, CA 94187
        </li>
      </ul>
    </div>
    <div class="band band--bottom"></div>
  </section>

  <section class="card card--brand" aria-label="Brand side">
    <div class="tab tab--right"></div>
    <div class="tab tab--left"></div>
    <div class="brand">
      <div class="brand__dot"></div>
      <p class="brand__name">VELDTMOOR<br>CAPITAL GROUP</p>
    </div>
  </section>

</main>
</body>
</html>
```